Clear Plastic Card Design

I am looking to have a business card designed from my logo icon. I am looking to match the style of a different business card I have attached in the files.
Looking for a card that is plastic, with layers of transparency in the shape of my logo icon (also attached in the files) - not a circle like the other card. The winning design will incorporate the red icon logo on the front and back and include the charity's name, "Light for the Weary Souls" in the same or similar font, as well as an email and phone number. For now, use the email: email@lightfortheweary-mail.org and the phone number 555-382-7194.
We like how the sample business card has transparency, partial and full opacity layers and a matching color scheme. Files will need to be in vector so that our business card printing company can work with it.
UPDATE:
We've some excellent designs in, thank you everyone! I got an early review from the owner, and he requested a minor redirect to find his perfect design. He wants the design to stand out by NOT being a rectangle. Try instead a circle, square, or best yet - something that falls in the outline of the logo icon, either fully or partially. Thank you, everyone!
Light for the Weary Souls text should be incorporated as well as a phone and email.

```html
<!DOCTYPE html>
<html lang="en">
<head>
<meta charset="utf-8">
<title>Light for the Weary Souls – Clear Card</title>
<link rel="stylesheet" href="https://fonts.googleapis.com/css2?family=Poppins:wght@300;400;500;600&family=Bodoni+Moda:wght@600&display=swap">
<style>
  :root {
    --stage: #e6ddd0;
    --label: #ffffff;
    --clear: rgba(255,255,255,0.32);
    --clear-edge: rgba(255,255,255,0.6);
    --band-top: #d2521f;
    --band-bottom: #e0662a;
    --mark-red: #c2141f;
    --mark-orange: #dd4a1e;
    --ink-dark: #2a2522;
    --ink-light: #f4e4d6;
    --back-red: #b3121b;
    --back-red-deep: #a10f16;
    --back-ink: #efe6dc;
  }
  * { margin: 0; padding: 0; box-sizing: border-box; }
  html, body { width: 1200px; height: 539px; overflow: hidden; }
  body { background: var(--stage); position: relative; font-family: "Poppins", sans-serif; }

  .side-label {
    position: absolute; top: 14px; width: 300px; text-align: center;
    font-family: "Bodoni Moda", serif; font-weight: 600; font-size: 38px;
    color: var(--label); text-shadow: 0 2px 6px rgba(0,0,0,0.25);
  }
  .side-label--front { left: 182px; }
  .side-label--back { left: 777px; }

  .card {
    position: absolute; top: 150px; width: 486px; height: 264px;
    border-radius: 20px; overflow: hidden;
  }
  .card--front {
    left: 79px; background: var(--clear);
    border: 1px solid var(--clear-edge);
  }
  .card--back {
    left: 659px;
    background: linear-gradient(135deg, var(--back-red) 0%, var(--back-red-deep) 100%);
  }

  .front-band {
    position: absolute; left: 0; right: 0; top: 132px; bottom: 0;
    background: linear-gradient(180deg, var(--band-top), var(--band-bottom));
    opacity: 0.92;
  }
  .front-emblem {
    position: absolute; left: 266px; top: 26px; width: 200px; height: 200px;
    background: linear-gradient(135deg, var(--mark-orange), var(--mark-red));
    opacity: 0.85; border-radius: 6px;
  }
  .org-name {
    position: absolute; left: 19px; top: 70px;
    font-weight: 400; font-size: 16px; line-height: 18px; color: var(--ink-dark);
  }
  .org-name__dot {
    display: inline-block; width: 10px; height: 10px; margin-right: 6px;
    background: var(--mark-red);
  }
  .person-name {
    position: absolute; left: 19px; top: 136px;
    font-size: 22px; color: var(--ink-light); letter-spacing: 0.5px;
  }
  .person-name strong { font-weight: 600; }
  .person-name span { font-weight: 300; }
  .person-role {
    position: absolute; left: 19px; top: 166px;
    font-size: 11.5px; font-weight: 500; color: var(--ink-light); letter-spacing: 0.4px;
  }
  .contact-list {
    position: absolute; left: 18px; top: 200px; list-style: none;
    font-size: 12.5px; font-weight: 300; color: var(--ink-light); letter-spacing: 0.3px;
  }
  .contact-list li { display: flex; align-items: center; height: 16px; }
  .contact-list svg { width: 11px; height: 11px; margin-right: 9px; fill: none; stroke: var(--ink-light); stroke-width: 1.6; }

  .back-name {
    position: absolute; left: 0; right: 0; top: 50%; transform: translateY(-50%);
    text-align: center; font-weight: 600; font-size: 28px; line-height: 36px;
    color: var(--back-ink);
  }
</style>
</head>
<body>
  <div class="side-label side-label--front">Front</div>
  <div class="side-label side-label--back">Back</div>

  <section class="card card--front">
    <div class="front-band"></div>
    <div class="front-emblem" aria-hidden="true"></div>
    <div class="org-name"><span class="org-name__dot"></span>Light for the<br>Weary Souls</div>
    <div class="person-name"><strong>Marta</strong> <span>Kovalova</span></div>
    <div class="person-role">Founder &amp; CEO</div>
    <ul class="contact-list">
      <li><svg viewBox="0 0 12 12"><path d="M2 1.5l2.2 0 .8 2.4-1.3 1a6 6 0 0 0 3.4 3.4l1-1.3 2.4.8v2.2c-5 .5-9-3.5-8.5-8.5z"/></svg>555-382-7194</li>
      <li><svg viewBox="0 0 12 12"><circle cx="6" cy="6" r="4.8"/><path d="M1.2 6h9.6M6 1.2c-2.4 2.6-2.4 7 0 9.6M6 1.2c2.4 2.6 2.4 7 0 9.6"/></svg>www.lightfortheweary.org</li>
      <li><svg viewBox="0 0 12 12"><rect x="1" y="2.5" width="10" height="7"/><path d="M1 2.5l5 4 5-4"/></svg>email@lightfortheweary-mail.org</li>
    </ul>
  </section>

  <section class="card card--back">
    <div class="back-name">Light for the<br>Weary Souls</div>
  </section>
</body>
</html>
```